Professional violinist needs business cards

I am trying to attract the following jobs:
-private violin lessons (primarily classical)
-performance gigs (weddings, birthday parties, funerals, etc.)
-collaborations with other artists (studio recordings, performances)

I want to communicate that I have a very high standard of excellence for my work, but I also love people and celebrations.
Values/style words I like are:
love, joy, peace, fun, beauty, authenticity, excellence, warmth, refined/sleek, free spirited. If that's too confusing, just ignore :)

I will attach my favorite business card template that I could find on Canva. The lines are supposed to be like a music staff, which I think is really cool, but I also don't want it to look too busy. I like the simple black and white--I think it looks sharp--but I also am open to other ideas. I also have seen business cards with pictures included that looked great, so I attached an image that could be used as well.

I am also attaching a file that I made of my initials that could be used as a logo, but I'm not sure if it should be included.

Information on the card:
-My name (18 letters total)
-"violinist"
-phone number, email, website

Thank you!

```html
<!DOCTYPE html>
<html lang="en">
<head>
<meta charset="utf-8">
<title>Helena Marwick – Violinist Business Card</title>
<link rel="stylesheet" href="https://fonts.googleapis.com/css2?family=Cinzel:wght@400&family=Dancing+Script:wght@500&family=Libre+Baskerville&display=swap">
<style>
  :root {
    --page-bg: #2a2a2b;
    --card-bg: #222629;
    --card-bg-deep: #1d2023;
    --staff-gap-bg: #212528;
    --staff-line: #3a3e42;
    --gold: #c8b48f;
    --gold-deep: #a98d5c;
    --ink-light: #e4e3e0;
    --photo-light: #6e665b;
    --photo-dark: #3b362f;
  }
  * { margin: 0; padding: 0; box-sizing: border-box; }
  html, body { width: 1200px; height: 1138px; overflow: hidden; background: var(--page-bg); }
  .canvas { position: relative; width: 1200px; height: 1138px; }

  .card {
    position: absolute;
    border-radius: 14px;
    overflow: hidden;
    background: linear-gradient(180deg, var(--card-bg) 0%, var(--card-bg-deep) 100%);
    box-shadow: 0 3px 8px rgba(0,0,0,0.45);
  }
  .card-front { left: 274px; top: 186px; width: 623px; height: 376px; }
  .card-back  { left: 277px; top: 607px; width: 618px; height: 375px; }

  .staff { position: absolute; left: 0; top: 93px; width: 100%; }
  .staff-line { position: absolute; left: 0; width: 100%; height: 1px; background: var(--staff-line); }

  .brand-mark {
    position: absolute; left: 0; width: 100%; top: 104px;
    text-align: center;
  }
  .brand-mark-text {
    display: inline-block;
    padding: 6px 18px;
    background: var(--staff-gap-bg);
    font-family: "Dancing Script", cursive; font-weight: 500;
    font-size: 30px; line-height: 1.2; color: var(--gold);
  }
  .front-name {
    position: absolute; left: 0; width: 100%; top: 196px;
    text-align: center;
    font-family: "Dancing Script", cursive; font-weight: 500;
    font-size: 36px; color: var(--ink-light);
  }
  .front-title {
    position: absolute; left: 0; width: 100%; top: 256px;
    text-align: center;
    font-family: "Cinzel", serif; font-size: 18px; letter-spacing: 3px;
    color: var(--ink-light);
  }

  .back-brand { position: absolute; left: 30px; top: 58px; width: 290px; }
  .back-brand-name {
    font-family: "Dancing Script", cursive; font-weight: 500;
    font-size: 23px; color: var(--ink-light); padding-left: 70px;
  }
  .back-brand-title {
    display: flex; align-items: center; gap: 8px; margin-top: 2px; padding-left: 70px;
    font-family: "Cinzel", serif; font-size: 11px; letter-spacing: 2px; color: var(--ink-light);
  }
  .back-brand-title::before, .back-brand-title::after {
    content: ""; flex: 1; height: 1px; background: var(--gold-deep);
  }
  .back-brand-dot {
    position: absolute; left: 0; top: 10px; width: 52px; height: 52px;
    border-radius: 50%; background: var(--gold); opacity: 0.9;
  }

  .contact-name {
    position: absolute; left: 31px; top: 192px;
    font-family: "Dancing Script", cursive; font-weight: 500;
    font-size: 24px; color: var(--ink-light);
  }
  .contact-list { position: absolute; left: 31px; top: 241px; list-style: none; }
  .contact-item {
    display: flex; align-items: center; height: 23.5px;
    font-family: "Libre Baskerville", serif; font-size: 14px; color: var(--ink-light);
  }
  .contact-icon { width: 14px; height: 14px; margin-right: 13px; fill: var(--ink-light); }
  .accent { color: var(--gold); }

  .photo-panel { position: absolute; right: 0; top: 0; width: 280px; height: 375px; }
</style>
</head>
<body>
<main class="canvas">

  <section class="card card-front" aria-label="Card front">
    <div class="staff">
      <span class="staff-line" style="top:0"></span>
      <span class="staff-line" style="top:23px"></span>
      <span class="staff-line" style="top:46px"></span>
      <span class="staff-line" style="top:69px"></span>
    </div>
    <div class="brand-mark"><span class="brand-mark-text">Helena Marwick</span></div>
    <h1 class="front-name">Helena Marwick</h1>
    <p class="front-title">VIOLINIST</p>
  </section>

  <section class="card card-back" aria-label="Card back">
    <div class="back-brand">
      <span class="back-brand-dot"></span>
      <div class="back-brand-name">Helena Marwick</div>
      <div class="back-brand-title">VIOLINIST</div>
    </div>

    <h2 class="contact-name">Helena Marwick</h2>
    <ul class="contact-list">
      <li class="contact-item">
        <svg class="contact-icon" viewBox="0 0 16 16"><path d="M1 5c0-2 3-3 7-3s7 1 7 3v1h-3V5H4v1H1zM3 7h10l1 7H2z"/></svg>
        +1 (555) 214-7730
      </li>
      <li class="contact-item">
        <svg class="contact-icon" viewBox="0 0 16 16"><path d="M8 1a5 5 0 0 0-5 5c0 4 5 9 5 9s5-5 5-9a5 5 0 0 0-5-5zm0 7a2 2 0 1 1 0-4 2 2 0 0 1 0 4z"/></svg>
        Riverton, MD
      </li>
      <li class="contact-item">
        <svg class="contact-icon" viewBox="0 0 16 16"><path d="M8 1a7 7 0 1 0 0 14A7 7 0 0 0 8 1zm0 1.5c.8 0 1.7 1.4 2 3.5H6c.3-2.1 1.2-3.5 2-3.5zM2.6 7h2.3v2H2.6zm3.3 0h4.2v2H5.9zm5.2 0h2.3v2h-2.3zM6 10h4c-.3 2.1-1.2 3.5-2 3.5S6.3 12.1 6 10z"/></svg>
        www.<span class="accent">HelenaMarwick</span>.com
      </li>
      <li class="contact-item">
        <svg class="contact-icon" viewBox="0 0 16 16"><path d="M1 3h14v10H1zm1.5 1.5v.3L8 9l5.5-4.2v-.3z"/></svg>
        Helena@HelenaMarwick.com
      </li>
    </ul>

    <svg class="photo-panel" viewBox="0 0 280 375" role="img" aria-label="Portrait photo of the violinist in a black dress holding her violin and bow beside a stone wall and railing">
      <defs>
        <linearGradient id="goldBand" x1="0" y1="0" x2="1" y2="1">
          <stop offset="0" stop-color="#d8c49c"/>
          <stop offset="1" stop-color="#a98d5c"/>
        </linearGradient>
        <linearGradient id="photoTone" x1="0" y1="0" x2="1" y2="1">
          <stop offset="0" stop-color="#6e665b"/>
          <stop offset="1" stop-color="#3b362f"/>
        </linearGradient>
      </defs>
      <path d="M50 0 C-10 110 -10 260 65 375 L280 375 L280 0 Z" fill="url(#goldBand)"/>
      <path d="M65 0 C5 110 5 260 75 375 L280 375 L280 0 Z" fill="url(#photoTone)"/>
    </svg>
  </section>

</main>
</body>
</html>
```